Brookmere Osteopathy flyer

I want a clean clear DL flyer (but also want an A4 poster) promoting a new Osteopathic business in a semi rural area in Tasmania (Australia).
It can have pictures like the examples attached to show people what Osteopathy is (its like Chiropractic and physiotherapy).
I am the sole practioner and am male, so any pictures would be best to be a white male if possible.
I've attached some wording, you can use all, or none of it
I don't have a phone number for the business yet
info@brookmereosteopathy.example
www.brookmereosteopathy.example
Target Market(s)
Australians, from tradies, professionals, babies to retired people
Industry/Entity Type
Health
Look and feel

```html
<!DOCTYPE html>
<html lang="en">
<head>
<meta charset="utf-8">
<title>Brookmere Osteopathy – Flyers</title>
<link rel="stylesheet" href="https://fonts.googleapis.com/css2?family=Open+Sans:wght@400;700;800&display=swap">
<style>
  :root{
    --navy:#0a0f57;
    --navy-deep:#050833;
    --blue:#0a93d8;
    --blue-head:#0a87cf;
    --sky:#6fcbed;
    --ink:#1d1d1f;
    --white:#ffffff;
    --paper:#ffffff;
  }
  *{box-sizing:border-box;margin:0;padding:0}
  html,body{width:1200px;height:848px;overflow:hidden;background:var(--paper)}
  body{font-family:"Open Sans",Arial,sans-serif;color:var(--ink);position:relative}
  .flyer{position:absolute;top:50px;height:750px;background:var(--white);overflow:hidden;box-shadow:0 0 3px rgba(0,0,0,.25)}
  .flyer--dl{left:147px;width:354px}
  .flyer--a4{left:525px;width:530px}
  .abs{position:absolute}
  .hero{position:absolute;left:0;top:0;width:100%;background:radial-gradient(ellipse at 40% 35%,#1a2fa8 0%,var(--navy) 45%,var(--navy-deep) 100%)}
  .portrait{position:absolute;background:linear-gradient(180deg,#b9b2ab 0%,#e9eef3 38%,#f4f6f8 100%);border-radius:40% 40% 0 0}
  .headline{position:absolute;color:var(--white);font-weight:800;letter-spacing:.3px}
  .headline em{font-style:normal;color:var(--blue)}
  .section-title{position:absolute;color:var(--blue-head);font-weight:800}
  .body-text{position:absolute;line-height:1.23}
  .rule{position:absolute;height:2px;background:var(--blue)}
  .tile{position:absolute;border-radius:12px;box-shadow:0 2px 4px rgba(0,0,0,.25)}
  .tile--skin{background:linear-gradient(135deg,#f3dcc8,#c99676)}
  .tile--baby{background:linear-gradient(135deg,#c79a82,#3f7fb8)}
  .tile--face{background:linear-gradient(135deg,#eef1f5,#a9806a 60%,#2a2a2e)}
  .tile--back{background:linear-gradient(135deg,#e7c6ac,#b98566 55%,#f1e4c0)}
  .conditions{position:absolute;list-style:none;border-left:1.5px solid var(--blue)}
  .conditions li{position:relative}
  .conditions li::before{content:"";position:absolute;left:-3.5px;top:50%;width:5px;height:5px;margin-top:-2px;border-radius:50%;background:var(--blue)}
  .contact{position:absolute;left:0;bottom:0;width:100%;color:var(--white)}
  .contact-title{position:absolute;font-weight:800}
  .contact-line{position:absolute;display:flex;align-items:center;white-space:nowrap}
  .contact-line svg{flex:none}
  .brand{position:absolute;display:flex;align-items:center;color:var(--white);font-weight:700;line-height:1.1}
  .brand-dot{flex:none;border:2px solid var(--white);border-radius:50%}
</style>
</head>
<body>

<!-- DL flyer -->
<article class="flyer flyer--dl">
  <div class="hero" style="height:267px"></div>
  <div class="portrait" role="img" aria-label="Smiling osteopath in white coat with arms crossed" style="left:165px;top:16px;width:189px;height:236px"></div>
  <svg class="abs" style="left:0;top:0" width="354" height="270" viewBox="0 0 354 270" aria-hidden="true">
    <path d="M0 0H132C108 20 100 70 60 76H0Z" fill="var(--blue)"/>
    <path d="M0 237H112C132 237 130 258 152 258H354V267H0Z" fill="var(--sky)"/>
  </svg>
  <div class="brand" style="left:8px;top:18px;width:110px;font-size:11px">
    <span class="brand-dot" style="width:12px;height:12px;margin-right:6px"></span>Brookmere Osteopathy
  </div>
  <h1 class="headline" style="left:16px;top:106px;font-size:24px;line-height:25px">You don’t<br>have to live<br>with <em>pain</em></h1>

  <h2 class="section-title" style="left:21px;top:287px;font-size:14px">What is Osteopathy?</h2>
  <p class="body-text" style="left:21px;top:304px;width:330px;font-size:13.6px;line-height:16.6px">Gentle treatment to reduce pain, improve mobility and help your body heal naturally using massage, joint movement &amp; stretching.</p>
  <div class="rule" style="left:21px;top:367px;width:314px"></div>

  <div class="tile tile--skin" role="img" aria-label="Hands massaging a patient's shoulder" style="left:12px;top:386px;width:74px;height:68px"></div>
  <div class="tile tile--baby" role="img" aria-label="Gentle treatment of a newborn's head" style="left:93px;top:386px;width:74px;height:68px"></div>
  <div class="tile tile--face" role="img" aria-label="Patient receiving neck treatment" style="left:12px;top:461px;width:74px;height:68px"></div>
  <div class="tile tile--back" role="img" aria-label="Hands treating a patient's lower back" style="left:96px;top:463px;width:74px;height:68px"></div>

  <h2 class="section-title" style="left:184px;top:403px;font-size:14px;line-height:16.5px">Osteopathy can<br>assist with:</h2>
  <ul class="conditions" style="left:183px;top:441px;font-size:12.6px;line-height:15.7px;padding-left:6px">
    <li>Back &amp; neck pain</li>
    <li>Sciatica &amp; disc issues</li>
    <li>Headaches</li>
    <li>Pregnancy discomfort</li>
    <li>Joint &amp; muscle problems</li>
  </ul>
  <div class="rule" style="left:21px;top:543px;width:314px"></div>

  <h2 class="section-title" style="left:21px;top:552px;font-size:14px">Who Do We Treat?</h2>
  <p class="body-text" style="left:21px;top:569px;width:330px;font-size:13.6px;line-height:16.6px">From active tradies and busy professionals to newborns and retirees — everyone is welcome. Treatments are always adjusted to suit your body, your lifestyle, and your goals.</p>

  <div class="contact" style="height:90px">
    <svg class="abs" style="left:0;top:0" width="354" height="90" viewBox="0 0 354 90" aria-hidden="true">
      <path d="M0 0H212C236 0 232 25 256 25H354V90H0Z" fill="var(--sky)"/>
    </svg>
    <h2 class="contact-title" style="left:21px;top:5px;font-size:13.5px">Contact Us:</h2>
    <div class="contact-line" style="left:26px;top:25px;font-size:13.6px;color:var(--ink)">
      <svg width="11" height="9" viewBox="0 0 11 9" style="margin-right:5px"><rect x=".5" y=".5" width="10" height="8" fill="var(--white)"/><path d="M.5 .5L5.5 5 10.5 .5" stroke="var(--sky)" fill="none"/></svg>info@brookmereosteopathy.example</div>
    <div class="contact-line" style="left:26px;top:42px;font-size:13.6px;color:var(--ink)">
      <svg width="11" height="11" viewBox="0 0 12 12" style="margin-right:5px"><circle cx="6" cy="6" r="5.3" fill="none" stroke="var(--white)" stroke-width="1.2"/><ellipse cx="6" cy="6" rx="2.3" ry="5.3" fill="none" stroke="var(--white)"/><path d="M.7 6H11.3M1.6 3.5H10.4M1.6 8.5H10.4" stroke="var(--white)"/></svg>www.brookmereosteopathy.example</div>
    <div class="contact-line" style="left:26px;top:58px;font-size:13.6px;color:var(--ink)">
      <svg width="11" height="12" viewBox="0 0 10 13" style="margin-right:5px"><path d="M5 12.5C5 12.5 9.5 7.5 9.5 4.7A4.5 4.5 0 0 0 .5 4.7C.5 7.5 5 12.5 5 12.5Z" fill="var(--white)"/><circle cx="5" cy="4.7" r="1.7" fill="var(--sky)"/></svg>Serving Brookmere and surrounding areas</div>
  </div>
</article>

<!-- A4 poster -->
<article class="flyer flyer--a4">
  <div class="hero" style="height:287px"></div>
  <div class="portrait" role="img" aria-label="Smiling osteopath in white coat with arms crossed" style="left:287px;top:20px;width:243px;height:256px"></div>
  <svg class="abs" style="left:0;top:0" width="530" height="290" viewBox="0 0 530 290" aria-hidden="true">
    <path d="M0 245H170C196 245 192 276 222 276H530V287H0Z" fill="var(--blue)"/>
  </svg>
  <h1 class="headline" style="left:24px;top:58px;font-size:36px;line-height:36px">You don’t<br>have to live<br>with <em>pain</em></h1>

  <h2 class="section-title" style="left:44px;top:296px;font-size:14px">What is Osteopathy?</h2>
  <p class="body-text" style="left:44px;top:313px;width:440px;font-size:13.6px;line-height:16.6px">Gentle treatment to reduce pain, improve mobility and help your body heal naturally using massage, joint movement &amp; stretching.</p>
  <div class="rule" style="left:116px;top:360px;width:313px"></div>

  <div class="tile tile--back" role="img" aria-label="Hands pressing on a patient's lower back" style="left:25px;top:380px;width:74px;height:68px"></div>
  <div class="tile tile--skin" role="img" aria-label="Hands massaging a patient's shoulder" style="left:106px;top:380px;width:74px;height:68px"></div>
  <div class="tile tile--baby" role="img" aria-label="Gentle treatment of a newborn's head" style="left:187px;top:380px;width:74px;height:68px"></div>
  <div class="tile tile--face" role="img" aria-label="Patient receiving a shoulder stretch" style="left:25px;top:455px;width:74px;height:68px"></div>
  <div class="tile tile--face" role="img" aria-label="Patient receiving neck treatment" style="left:106px;top:454px;width:74px;height:68px"></div>
  <div class="tile tile--back" role="img" aria-label="Hands treating a patient's abdomen" style="left:190px;top:456px;width:74px;height:68px"></div>

  <h2 class="section-title" style="left:288px;top:376px;font-size:18px;line-height:21.5px">Osteopathy can<br>assist with:</h2>
  <ul class="conditions" style="left:287px;top:423px;font-size:16.6px;line-height:20px;padding-left:7px">
    <li>Back &amp; neck pain</li>
    <li>Sciatica &amp; disc issues</li>
    <li>Headaches</li>
    <li>Pregnancy discomfort</li>
    <li>Joint &amp; muscle problems</li>
  </ul>
  <div class="rule" style="left:116px;top:536px;width:313px"></div>

  <h2 class="section-title" style="left:44px;top:545px;font-size:14px">Who Do We Treat?</h2>
  <p class="body-text" style="left:44px;top:562px;width:450px;font-size:13.6px;line-height:16.6px">From active tradies and busy professionals to newborns and retirees everyone is welcome. Treatments are always adjusted to suit your body, your lifestyle, and your goals.</p>

  <div class="contact" style="height:102px;background:var(--blue);border-radius:40px 40px 0 0">
    <div class="brand" style="left:40px;top:30px;width:118px;font-size:14px">
      <span class="brand-dot" style="width:16px;height:16px;margin-right:7px"></span>Brookmere Osteopathy
    </div>
    <h2 class="contact-title" style="left:181px;top:3px;font-size:24px">Contact Us:</h2>
    <div class="contact-line" style="left:183px;top:38px;font-size:16.2px">
      <svg width="13" height="10" viewBox="0 0 11 9" style="margin-right:5px"><rect x=".5" y=".5" width="10" height="8" fill="var(--white)"/><path d="M.5 .5L5.5 5 10.5 .5" stroke="var(--blue)" fill="none"/></svg>info@brookmereosteopathy.example</div>
    <div class="contact-line" style="left:183px;top:57px;font-size:16.2px">
      <svg width="13" height="13" viewBox="0 0 12 12" style="margin-right:5px"><circle cx="6" cy="6" r="5.3" fill="none" stroke="var(--white)" stroke-width="1.2"/><ellipse cx="6" cy="6" rx="2.3" ry="5.3" fill="none" stroke="var(--white)"/><path d="M.7 6H11.3M1.6 3.5H10.4M1.6 8.5H10.4" stroke="var(--white)"/></svg>www.brookmereosteopathy.example</div>
    <div class="contact-line" style="left:183px;top:76px;font-size:16.2px">
      <svg width="12" height="14" viewBox="0 0 10 13" style="margin-right:6px"><path d="M5 12.5C5 12.5 9.5 7.5 9.5 4.7A4.5 4.5 0 0 0 .5 4.7C.5 7.5 5 12.5 5 12.5Z" fill="var(--white)"/><circle cx="5" cy="4.7" r="1.7" fill="var(--blue)"/></svg>Serving Brookmere and surrounding areas</div>
  </div>
</article>

</body>
</html>
```